Marlowe Group needs a business card

I would like the card to be simple but modern and elegant.
I like black and white.
or black and gold.
we are a private finance lender and also are involved in property and property developments.

please look at the business card photos i provided i would like M.G only one one side and all the other details on the other side use fonts that tie in with my theme.

Industry/Entity Type

Finance

Contact Information for Business Card

Marlowe Group (M.G) Daniel Marlowe M: 0413586207 E: danmarl@inboxmail.test

Font styles to use
Other font styles liked:
• Use fonts that would reflect our business

Colors
000000
ffffff

Requirements
Must have
• one side of details
• other side has either M.G or Marlowe Group like in the photos provided

```html
<!DOCTYPE html>
<html lang="en">
<head>
<meta charset="utf-8">
<title>Marlowe Group — Business Card</title>
<link rel="stylesheet" href="https://fonts.googleapis.com/css2?family=Hind:wght@400&display=swap">
<style>
  :root {
    --backdrop: #e9e7e4;
    --card: #ffffff;
    --ink: #3f3f3f;
    --ink-strong: #2a2a2a;
    --accent-bar: #444444;
  }
  * { margin: 0; padding: 0; box-sizing: border-box; }
  html, body {
    width: 1200px;
    height: 900px;
    overflow: hidden;
    background: var(--backdrop);
  }
  .stage {
    position: relative;
    width: 1200px;
    height: 900px;
  }
  .card {
    position: absolute;
    left: 368px;
    top: 158px;
    width: 652px;
    height: 402px;
    background: var(--card);
    border-radius: 0 201px 201px 0;
    box-shadow: 0 10px 30px rgba(0, 0, 0, 0.12);
  }
  .card__bar {
    position: absolute;
    left: 0;
    top: 112px;
    width: 17px;
    height: 176px;
    background: var(--accent-bar);
  }
  .card__name {
    position: absolute;
    left: 44px;
    top: 106px;
    font-family: "Hind", sans-serif;
    font-weight: 400;
    font-size: 28px;
    line-height: 1.2;
    letter-spacing: 0.5px;
    color: var(--ink);
  }
  .contact {
    position: absolute;
    left: 44px;
    top: 238px;
    list-style: none;
    font-family: "Hind", sans-serif;
    font-weight: 400;
    font-size: 21px;
    line-height: 28px;
    letter-spacing: 0.4px;
    color: var(--ink);
  }
  .contact__item {
    display: flex;
    align-items: center;
    gap: 8px;
  }
  .contact__icon {
    width: 13px;
    height: 17px;
    flex: none;
  }
  .brand {
    position: absolute;
    left: 350px;
    top: 172px;
    display: flex;
    align-items: center;
    gap: 12px;
  }
  .brand__mark {
    width: 34px;
    height: 34px;
    background: var(--ink-strong);
    flex: none;
  }
  .brand__name {
    font-family: "Hind", sans-serif;
    font-weight: 400;
    font-size: 30px;
    line-height: 1;
    color: var(--ink-strong);
    white-space: nowrap;
  }
</style>
</head>
<body>
<main class="stage">
  <section class="card" aria-label="Marlowe Group business card">
    <div class="card__bar"></div>
    <h1 class="card__name">Daniel Marlowe</h1>
    <ul class="contact">
      <li class="contact__item">
        <svg class="contact__icon" viewBox="0 0 16 20" aria-hidden="true">
          <rect x="2.5" y="1" width="11" height="18" rx="2" fill="none" stroke="var(--ink)" stroke-width="2"/>
          <rect x="6" y="15" width="4" height="1.6" fill="var(--ink)"/>
        </svg>
        <span>0413586207</span>
      </li>
      <li class="contact__item">
        <svg class="contact__icon" viewBox="0 0 16 20" aria-hidden="true">
          <rect x="1" y="5" width="14" height="10" fill="var(--ink)"/>
          <path d="M1 5 L8 11 L15 5" fill="none" stroke="#ffffff" stroke-width="1.4"/>
        </svg>
        <span>danmarl@inboxmail.test</span>
      </li>
    </ul>
    <div class="brand">
      <span class="brand__mark" aria-hidden="true"></span>
      <span class="brand__name">Marlowe Group</span>
    </div>
  </section>
</main>
</body>
</html>
```